Landing Page Design for Adult Dating Age Verification (18+)

The objective of this task is to design a visually appealing pre-landing page for the adult dating site "Quillmera (site: https://quillmera.com/)" with an age verification mechanism. The pre-landing page will feature two buttons that redirect visitors to the main offer. The design should also include a footer block that includes links to the terms of use, privacy policy, and contact us pages.

Design Requirements:
Develop an age verification section prominently displayed on the pre-landing page.
Design the section to include two buttons labeled "Yes" and "No" for visitors to confirm their age.
Ensure the section is visually appealing and clearly communicates the purpose of age verification.

Visual Appeal:
Create a visually appealing design that aligns with the branding and theme of the "Quillmera" adult dating site.
Use suitable color schemes, typography, and graphics to enhance the overall visual appeal of the pre-landing page.

Layout and Navigation:
Design an engaging and intuitive layout that encourages visitors to interact with the page and proceed to the main offer.
Ensure clear and visible navigation elements that direct visitors to the main offer or provide additional information.

Responsive Design:
Develop a responsive design that provides a seamless user experience across various devices, including desktop and mobile.
Ensure the design elements and layout adapt well to different screen sizes and resolutions.

File Formats and Assets:
Deliver the final design in PSD, AI, or Sketch format, ensuring that the files are well-organized and layered.
Include any necessary images or assets used in the design, ensuring they are of high quality and optimized for web use.

```html
<!DOCTYPE html>
<html lang="en">
<head>
<meta charset="UTF-8">
<title>Quillmera — Age Verification</title>
<link rel="stylesheet" href="https://fonts.googleapis.com/css2?family=Libre+Caslon+Text:wght@400;700&display=swap">
<style>
  :root {
    --ink: #ffffff;
    --lilac: #d2b4d8;
    --rose: #e7b6c8;
    --night: #0b131a;
    --hero-top: #2b3a48;
    --hero-mid: #4b4f6a;
    --hero-low: #30403f;
    --panel: rgba(150, 140, 210, 0.32);
    --btn-text: #1c2530;
  }
  * { box-sizing: border-box; margin: 0; padding: 0; }
  html, body { width: 1200px; height: 789px; overflow: hidden; }
  body {
    position: relative;
    font-family: "Libre Caslon Text", Georgia, serif;
    color: var(--ink);
    background: var(--night);
  }
  .hero {
    position: absolute; left: 0; top: 0; width: 1200px; height: 684px;
    background:
      radial-gradient(ellipse 380px 260px at 620px 380px, rgba(120,110,170,0.55), transparent 70%),
      radial-gradient(ellipse 300px 200px at 1050px 300px, rgba(110,130,150,0.45), transparent 70%),
      linear-gradient(180deg, var(--hero-top) 0%, var(--hero-mid) 45%, var(--hero-low) 100%);
  }
  .brand {
    position: absolute; display: flex; align-items: center; gap: 10px;
    color: var(--ink); text-decoration: none; font-weight: 400; line-height: 1;
  }
  .brand-dot { border-radius: 50%; background: var(--lilac); flex: none; }
  .site-header .brand { left: 111px; top: 34px; font-size: 40px; }
  .site-header .brand-dot { width: 44px; height: 44px; }
  .main-nav {
    position: absolute; top: 43px; left: 763px;
    display: flex; gap: 30px; font-size: 16px;
  }
  .main-nav a { color: var(--ink); text-decoration: none; display: flex; align-items: center; gap: 8px; }
  .main-nav svg { width: 22px; height: 22px; }
  .age-gate {
    position: absolute; left: 309px; top: 188px; width: 581px; height: 352px;
    border-radius: 52px;
    background: var(--panel);
    border: 2px solid var(--rose);
    text-align: center;
    backdrop-filter: blur(2px);
  }
  .age-gate h1 {
    margin-top: 50px; font-size: 43px; font-weight: 400; line-height: 60px;
  }
  .choices { display: flex; justify-content: center; gap: 32px; margin-top: 30px; }
  .choice {
    width: 132px; height: 54px; border-radius: 27px;
    display: flex; align-items: center; justify-content: center; gap: 8px;
    font-family: inherit; font-size: 20px; text-decoration: none;
  }
  .choice-yes { background: var(--ink); color: var(--btn-text); }
  .choice-no { border: 2px solid var(--ink); color: var(--ink); }
  .remember {
    margin-top: 24px; display: inline-flex; align-items: center; gap: 8px; font-size: 15px;
  }
  .remember .box { width: 12px; height: 12px; border: 1.5px solid var(--ink); border-radius: 2px; }
  .site-footer {
    position: absolute; left: 0; top: 684px; width: 1200px; height: 105px; background: var(--night);
  }
  .footer-links { position: absolute; left: 69px; top: 43px; display: flex; gap: 25px; font-size: 13px; }
  .footer-links a { color: var(--ink); text-decoration: none; }
  .site-footer .brand { left: 458px; top: 32px; font-size: 41px; }
  .site-footer .brand-dot { width: 40px; height: 40px; background: var(--ink); }
  .copyright { position: absolute; left: 817px; top: 45px; font-size: 13px; }
</style>
</head>
<body>
  <section class="hero" role="img" aria-label="Dim bedroom photograph with a woman in lingerie lying on a bed"></section>

  <header class="site-header">
    <a class="brand" href="https://quillmera.com/"><span class="brand-dot"></span>Quillmera</a>
    <nav class="main-nav">
      <a href="#"><svg viewBox="0 0 22 22"><circle cx="11" cy="11" r="11" fill="#fff"/><path d="M9 7h6v8H9M6 11h6M10 8.5l2.5 2.5L10 13.5" fill="none" stroke="#2b3a48" stroke-width="1.6"/></svg>Sign In</a>
      <a href="#"><svg viewBox="0 0 22 22"><circle cx="11" cy="11" r="11" fill="#fff"/><path d="M9.5 12.5l3-3M8.5 10l-1.5 1.5a2 2 0 0 0 3 3L11.5 13M13.5 12l1.5-1.5a2 2 0 0 0-3-3L10.5 9" fill="none" stroke="#2b3a48" stroke-width="1.6"/></svg>Join Now</a>
      <a href="#"><svg viewBox="0 0 22 22"><circle cx="11" cy="11" r="11" fill="#fff"/><g fill="none" stroke="#2b3a48" stroke-width="1.2"><circle cx="11" cy="11" r="6"/><ellipse cx="11" cy="11" rx="2.6" ry="6"/><path d="M5 11h12M6 8h10M6 14h10"/></g></svg>English</a>
    </nav>
  </header>

  <main class="age-gate">
    <h1>Are you over 18 years<br>of age?</h1>
    <div class="choices">
      <a class="choice choice-yes" href="#"><svg width="22" height="20" viewBox="0 0 22 20"><path d="M11 19S1 12.5 1 6.5A5 5 0 0 1 11 4a5 5 0 0 1 10 2.5C21 12.5 11 19 11 19z" fill="var(--lilac)"/></svg>Yes</a>
      <a class="choice choice-no" href="#">No</a>
    </div>
    <label class="remember"><span class="box"></span>Remember Me</label>
  </main>

  <footer class="site-footer">
    <nav class="footer-links">
      <a href="#">Privacy Policy</a>
      <a href="#">Terms &amp; Conditions</a>
      <a href="#">Contact Us</a>
    </nav>
    <a class="brand" href="https://quillmera.com/"><span class="brand-dot"></span>Quillmera</a>
    <p class="copyright">Copyrights@2023 Quillmera. All Rights Reserved</p>
  </footer>
</body>
</html>
```